Small Business Consulting Firm Needs Letterhead

We need a letterhead for our company "Brightpath Plus". Our company does outbound calling and mailing to business owner's companies who have taken high interest loans. These loans tend to put these businesses in a big financial bind short term, and we help them find better financial options. We would like the design to match our colors of our logo. Headers and footers would look nice, but we are open. We would want it to include our address, website, phone, and email info. Our address - 2000 E. Lamar Blvd. Suite 600Website - www.safeguardtoday.comEmail - info@safeguardtoday.comPhone - 855-726-1938
Industry/Entity Type
Financial Planning
Look and feel
Each slider illustrates characteristics of the customer's brand and the style your logo design should communicate.

```html
<!DOCTYPE html>
<html lang="en">
<head>
<meta charset="utf-8">
<title>Brightpath Plus Letterhead</title>
<link rel="stylesheet" href="https://fonts.googleapis.com/css2?family=Arimo:wght@400;700&display=swap">
<style>
  :root {
    --brand-blue: #0a72c0;
    --brand-green: #66a23a;
    --ink: #1e1e1e;
    --ink-soft: #444;
    --paper: #ffffff;
    --signature-tone: #e6e6e6;
  }
  * { margin: 0; padding: 0; box-sizing: border-box; }
  html, body { width: 969px; height: 1200px; overflow: hidden; background: var(--paper); }
  body { font-family: "Arimo", Arial, sans-serif; color: var(--ink); }

  .letterhead { position: relative; width: 969px; height: 1200px; background: var(--paper); }

  .header-band { position: absolute; left: 0; top: 0; width: 100%; height: 5px; background: var(--brand-blue); }
  .header-rule { position: absolute; left: 0; top: 6px; width: 100%; height: 1px; background: var(--brand-green); }

  .brand { position: absolute; top: 60px; left: 0; width: 100%; text-align: center; }
  .brand-square { display: block; width: 70px; height: 70px; margin: 0 auto 26px; background: var(--brand-green); }
  .brand-name { font-size: 26px; font-weight: 400; letter-spacing: 2px; text-transform: uppercase; color: var(--ink-soft); }

  .salutation { position: absolute; left: 133px; top: 292px; font-size: 18px; }

  .letter-body { position: absolute; left: 133px; top: 362px; width: 703px; font-size: 18px; line-height: 23.8px; text-align: justify; }
  .letter-body p { margin-bottom: 21px; }

  .closing { position: absolute; left: 133px; top: 860px; font-size: 18px; }
  .signature { position: absolute; left: 136px; top: 893px; width: 92px; height: 62px; background: var(--signature-tone); border-radius: 4px; }

  .address { position: absolute; top: 1061px; left: 0; width: 100%; text-align: center; font-size: 18px; }

  .contact-line { position: absolute; top: 1098px; left: 0; width: 100%; display: flex; align-items: center; font-size: 18px; }
  .contact-line .rule { flex: 1; height: 2px; background: var(--brand-blue); }
  .contact-line .details { padding: 0 8px; white-space: nowrap; }
  .contact-line .label { color: var(--brand-blue); font-weight: 700; }
  .contact-line .gap { display: inline-block; width: 16px; }

  .web-band { position: absolute; top: 1138px; left: 0; width: 100%; height: 31px; background: var(--brand-green); color: var(--paper); text-align: center; font-size: 22px; line-height: 31px; letter-spacing: 8px; }
</style>
</head>
<body>
<main class="letterhead">
  <div class="header-band"></div>
  <div class="header-rule"></div>

  <header class="brand">
    <span class="brand-square"></span>
    <div class="brand-name">Brightpath Plus</div>
  </header>

  <p class="salutation">Dear :</p>

  <section class="letter-body">
    <p>Lorem ipsum dolor sit amet, consectetur adipiscing elit. Aenean ut ipsum eget massa hendrerit vestibulum vel in velit. Donec pretium neque velit.</p>
    <p>Aliquam porta lectus nec mauris ornare venenatis. Vivamus non est turpis, et cursus sem. Mauris vehicula erat in diam auctor at bibendum nisl lacinia.</p>
    <p>Morbi imperdiet neque vehicula nunc convallis gravida. Vestibulum iaculis pretium placerat. Integer consequat, est sit amet facilisis eleifend, nibh nibh varius orci, eget dapibus arcu dui non purus. Pellentesque in magna mauris. Duis enim sapien, dictum vitae condimentum a, pulvinar vel lacus. Mauris et molestie nibh. Vestibulum vitae nulla at metus elementum porta sit amet interdum elit. Nulla sollicitudin neque eu nulla volutpat congue.</p>
    <p>Etiam pellentesque, velit id dapibus fermentum, turpis sapien ornare dui, ac tincidunt ligula odio congue purus. Nunc sed ante dui, in porta lectus. Cras nec sem lorem. In hac habitasse platea dictumst. Maecenas id diam quis dui porta tristique. Sed id egestas felis. Donec ullamcorper mattis posuere. Phasellus fermentum eleifend tortor vel dapibus. Vestibulum ante ipsum.</p>
  </section>

  <p class="closing">Sincerely,</p>
  <div class="signature" role="img" aria-label="Handwritten signature"></div>

  <footer>
    <p class="address">Add: 4170 W. Corwin Ave. Suite 310</p>
    <div class="contact-line">
      <span class="rule"></span>
      <span class="details"><span class="label">Phone</span> - 855-726-1938<span class="gap"></span><span class="label">Email</span> - info@brightpathplus.com</span>
      <span class="rule"></span>
    </div>
    <div class="web-band">www.brightpathplus.com</div>
  </footer>
</main>
</body>
</html>
```